Website Design for Solar Panel Company

We are working with a company called VoltaNix.

Some sites to use for content/competitors and inspiration:
https://www.brivaloo.com
https://prod.aws-prod.kelmatrix.com
https://tovarqueworks.net
https://www.quorvex.com/solarpanels

Thank you for taking the time to consider designing a website for us. We are web developers based in Stockton, CA, USA. Most of our projects go through the same process. Understanding this process may help you win a project with us. We custom-code all of our websites in-house. We don’t have any requirements as to what tools you use for your design, but we prefer Figma files. For any design that we label as four-stars, we send it to the client for review. The client picks the final design they want us to use. Once we complete this process, we will continue to show additional clients all the four-star sites and purchase them later. Your designs will have multiple chances to sell. For better chances of success, we ask that you follow these guidelines.

IMAGES:
If you use any images or icons in the design, we ask that you have a link to the asset so we can purchase the image/icon. Most of the designs we submit do not have the customer’s images on them unless they have some great images. Be creative; show us the feeling you are trying to portray with your image choices. Use any royalty-free site you choose. We subscribe to Pendrel and mainly use their images, but we can purchase images outside of Pendrel. PLEASE NOTE: we will not submit designs to clients with watermarks on the images.

FONTS:
We ask that you identify the fonts used in the design. This can be done in a message if you want. We typically use Google Fonts and Pendrel Fonts.

CONTENT:
We're always open to different content and ideas. We often submit designs with stock images so the client can see our vision. We typically take pictures after the website launch to use their images with our vision. Lorem Ipsum is fine for paragraphs, but we ask that you write the headers in correct English. We want to be able to show the vision and identify the sections of the website.

INSPIRATION:
We typically add a couple of links in the brief of websites we like to help you get started in your design.

REVISIONS:
We do not often ask for revisions of the designs unless we see something in the design that may not appeal to the client. If there are slight changes that we want to make, we do that in the development process.

FEEDBACK:
We rarely give feedback on designs during the design process. We are working on many website projects and do not have the time to provide feedback. We usually respond if your request is well thought out and asks specific questions, but a note asking “feedback, please” usually goes unanswered.

```html
<!DOCTYPE html>
<html lang="en">
<head>
<meta charset="utf-8">
<title>VoltaNix — Solar Energy</title>
<link rel="stylesheet" href="https://fonts.googleapis.com/css2?family=Red+Hat+Display:wght@400;500;700;800&family=Merriweather:wght@300;400&display=swap">
<style>
:root{
  --green:#23900c;
  --navy:#1c3f70;
  --footer:#1b4d88;
  --light:#eef3f8;
  --ink:#343a40;
  --muted:#8b9097;
  --white:#ffffff;
}
*{box-sizing:border-box;margin:0;padding:0}
html,body{width:1200px;height:3839px;overflow:hidden}
body{position:relative;background:var(--white);font-family:'Merriweather',Georgia,serif;color:var(--ink)}
.abs{position:absolute}
h1,h2,h3,.sans{font-family:'Red Hat Display',Arial,sans-serif}

/* hero */
.hero{left:0;top:0;width:1200px;height:563px;background:linear-gradient(160deg,#6b4a38 0%,#3b5a93 30%,#5b77a8 50%,#8a6a56 75%,#6d4c3c 100%)}
.nav{left:0;top:0;width:1200px;height:68px;border-bottom:1px solid rgba(255,255,255,.35)}
.brand{left:249px;top:14px;color:var(--white);font-family:'Red Hat Display',sans-serif;font-weight:800;font-size:30px;letter-spacing:.5px}
.menu{left:410px;top:26px;display:flex;gap:30px}
.menu a{color:var(--white);font-family:'Red Hat Display',sans-serif;font-size:13px;text-decoration:none;letter-spacing:.3px}
.btn{background:var(--green);color:var(--white);font-family:'Red Hat Display',sans-serif;font-weight:700;font-size:14px;display:flex;align-items:center;justify-content:center;text-decoration:none;border-radius:2px}
.nav-btn{left:781px;top:17px;width:172px;height:36px}
.hero-card{left:601px;top:154px;width:481px;height:292px;background:rgba(34,110,20,.82);text-align:center;color:var(--white);padding-top:33px}
.hero-card h1{font-size:37px;line-height:45px;font-weight:800}
.hero-card p{font-size:11.5px;line-height:18px;margin:20px auto 0;width:370px}
.hero-btn{position:relative;margin:21px auto 0;width:152px;height:49px;font-size:14px}

/* about */
.about{left:0;top:490px;width:1200px;height:760px;background:var(--light)}
.title{width:1200px;left:0;text-align:center;font-size:30px;line-height:40px;font-weight:700;color:#33383d}
.photo-circle{left:250px;top:764px;width:350px;height:350px;border-radius:50%;border:9px solid var(--green);background:radial-gradient(circle at 50% 45%,#3d4a62 0%,#6a6f76 40%,#8d7d64 100%)}
.about-text{left:666px;top:800px;width:280px;font-size:11px;line-height:18px;color:var(--muted);font-weight:300}
.about-text p+p{margin-top:17px}
.socials{left:668px;top:1022px;display:flex;gap:24px}
.socials span{width:38px;height:38px;border-radius:50%;background:var(--navy);border:3px solid #cfd9e6}

/* features */
.features{left:0;top:1430px;width:1200px;display:flex;justify-content:center;gap:0}
.feature{width:238px;text-align:center}
.feature svg{display:block;margin:0 auto}
.feature h3{font-size:14.5px;font-weight:700;letter-spacing:.3px;margin-top:34px;color:#2b2f33}
.feature p{font-size:9.5px;line-height:15px;color:var(--muted);margin:20px auto 0;width:180px;font-weight:300}

/* contact */
.contact{left:0;top:1717px;width:1200px;height:884px;background:linear-gradient(135deg,#15301e 0%,#1d2a3c 35%,#2a3442 60%,#1a2330 100%)}
.form-box{left:195px;top:1856px;width:810px;height:659px;background:rgba(22,62,112,.82);border:1px solid rgba(120,160,210,.35)}
.form-box h2{position:absolute;left:0;width:100%;top:76px;text-align:center;color:var(--white);font-size:28px;font-weight:800}
.lbl{font-family:'Red Hat Display',sans-serif;font-size:11px;font-weight:700;color:var(--white);letter-spacing:.3px}
.lbl b{color:#e23b3b;margin-left:6px}
.field{height:34px;border:1px solid rgba(255,255,255,.6);background:rgba(255,255,255,.14);border-radius:3px}

/* split */
.split-img{width:600px;height:413px}
.split-text h2{font-size:30px;font-weight:700;color:#2f3438}
.split-text p{font-size:11px;line-height:18px;color:var(--muted);font-weight:300;margin-top:17px;width:350px}

/* footer */
.footer{left:0;top:3426px;width:1200px;height:413px;background:var(--footer);color:var(--white)}
.col{top:3486px}
.col h4{font-family:'Red Hat Display',sans-serif;font-size:14px;font-weight:700;letter-spacing:.2px;margin-bottom:18px}
.col li{list-style:none;font-size:11px;line-height:25.5px;font-weight:300}
.col li.icon{display:flex;align-items:center;gap:9px;line-height:34.5px}
.col li.icon i{width:22px;height:22px;border-radius:50%;background:var(--white)}
.rule{left:178px;top:3780px;width:834px;height:1px;background:rgba(255,255,255,.5)}
.copy{left:178px;top:3800px;font-size:9px;font-family:'Red Hat Display',sans-serif;font-weight:700}
.legal{left:876px;top:3800px;font-size:9px;font-family:'Red Hat Display',sans-serif;font-weight:500}
</style>
</head>
<body>

<div class="abs hero" role="img" aria-label="Photo of a tiled roof fitted with blue solar panels"></div>
<header class="abs nav">
  <div class="abs brand">VoltaNix</div>
  <nav class="abs menu"><a href="#">HOMEOWNERS</a><a href="#">BUILDERS</a><a href="#">DEALERS</a><a href="#">BLOG</a></nav>
  <a class="abs btn nav-btn" href="#">FREE CONULTATION</a>
</header>
<section class="abs hero-card">
  <h1>Save your money<br>with cleaner enregy</h1>
  <p>Use solar energy to power your home and reduce your dependence on the grid. Purchase solar at the lowest price of any national provide</p>
  <a class="btn hero-btn" href="#">FREE CONSULTAION</a>
</section>

<section class="abs about"></section>
<svg class="abs" style="left:0;top:480px" width="1200" height="90" viewBox="0 0 1200 90" preserveAspectRatio="none"><path d="M0 83 C300 70 700 60 1200 10 L1200 90 L0 90Z" fill="#eef3f8"/></svg>
<h2 class="abs title" style="top:620px">Solve your problems<br>with VoltaNix</h2>
<div class="abs photo-circle" role="img" aria-label="Photo of installers carrying a solar panel across a site"></div>
<div class="abs about-text">
  <p>VoltaNix is changing the way our world is powered by making solar and storage more accessible to everyone.</p>
  <p>With nearly 40 years of dedicated solar experience, we're the top-rated* U.S. solar company with over 15,000 five-star reviews.*</p>
  <p>If you're considering solar, energy storage, or EV charging for your home, make sure you talk to Kelmatrix</p>
</div>
<div class="abs socials"><span></span><span></span><span></span></div>
<svg class="abs" style="left:0;top:1160px" width="1200" height="110" viewBox="0 0 1200 110" preserveAspectRatio="none"><path d="M0 8 C150 40 230 85 420 70 C650 50 800 -10 1200 60 L1200 110 L0 110Z" fill="#fff"/></svg>

<h2 class="abs title" style="top:1290px">Professional suplier<br>of solar panel</h2>
<div class="abs features">
  <div class="feature">
    <svg width="124" height="124" viewBox="0 0 124 124" role="img" aria-label="Savings calculator icon"><path d="M52 5 A57 57 0 1 0 72 5" fill="none" stroke="#1c3f70" stroke-width="2.5"/><rect x="38" y="38" width="48" height="44" rx="4" fill="#d9efd3" stroke="#23900c" stroke-width="2"/></svg>
    <h3>SAVINGS CALCULATOR</h3>
    <p>Our intuitive solar calculator lets you see an estimate of how much you can save on your electric bill and how much backup storage you may need.</p>
  </div>
  <div class="feature">
    <svg width="124" height="124" viewBox="0 0 124 124" role="img" aria-label="Online estimate icon"><path d="M52 5 A57 57 0 1 0 72 5" fill="none" stroke="#1c3f70" stroke-width="2.5"/><rect x="38" y="36" width="48" height="50" rx="4" fill="#d9efd3" stroke="#23900c" stroke-width="2"/></svg>
    <h3>ONLINE ESTIMATE</h3>
    <p>Fill out a form and see how much you can save on electricity by installing home solar panels with the top-rated solar company in the U.S.*</p>
  </div>
  <div class="feature">
    <svg width="124" height="124" viewBox="0 0 124 124" role="img" aria-label="Virtual consultation icon"><path d="M52 5 A57 57 0 1 0 72 5" fill="none" stroke="#1c3f70" stroke-width="2.5"/><rect x="36" y="40" width="52" height="42" rx="4" fill="#d9efd3" stroke="#23900c" stroke-width="2"/></svg>
    <h3>VIRTUAL CONSULTATION</h3>
    <p>Want to find your perfect system without leaving home? Set up a free online appointment with one of our solar pros and get in-depth advice without worry.</p>
  </div>
</div>

<section class="abs contact" role="img" aria-label="Photo of a worker in gloves fixing rows of solar panels"></section>
<svg class="abs" style="left:0;top:1716px" width="1200" height="102" viewBox="0 0 1200 102" preserveAspectRatio="none"><path d="M0 0 L1200 0 L1200 100 L0 2Z" fill="#fff"/></svg>
<form class="abs form-box">
  <h2>Contact Us</h2>
  <span class="abs lbl" style="left:128px;top:174px">FIRST NAME<b>*</b></span>
  <span class="abs lbl" style="left:440px;top:174px">LAST NAME</span>
  <div class="abs field" style="left:128px;top:203px;width:241px"></div>
  <div class="abs field" style="left:440px;top:203px;width:240px"></div>
  <span class="abs lbl" style="left:128px;top:296px">EMAIL</span>
  <span class="abs lbl" style="left:440px;top:296px">PHONE<b>*</b></span>
  <div class="abs field" style="left:128px;top:325px;width:241px"></div>
  <div class="abs field" style="left:440px;top:325px;width:240px"></div>
  <span class="abs lbl" style="left:128px;top:417px">ADDRESS<b>*</b></span>
  <div class="abs field" style="left:128px;top:446px;width:552px"></div>
  <a class="abs btn" style="left:128px;top:535px;width:552px;height:40px" href="#">GET STARTED</a>
</form>

<div class="abs split-img" style="left:0;top:2601px;background:linear-gradient(135deg,#2f3a4c 0%,#3f4c62 45%,#6b7485 70%,#40495a 100%)" role="img" aria-label="Photo of a technician in a green shirt mounting solar panels"></div>
<div class="abs split-text" style="left:636px;top:2658px">
  <h2>Monitor your home solar</h2>
  <p style="margin-top:28px">With nearly 40 years of dedicated solar experience, we're the top-rated* U.S. solar company with over 15,000 five-star reviews.*</p>
  <p>If you're considering solar, energy storage, or EV charging for your home, make sure you talk to Kelmatrix.</p>
  <p>With nearly 40 years of dedicated solar experience, we're the top-rated* U.S. solar company with over 15,000 five-star reviews.*</p>
  <p>If you're considering solar, energy storage, or EV charging for your home, make sure you talk to Kelmatrix</p>
</div>
<div class="abs split-text" style="left:210px;top:3071px">
  <h2>Seamless backup power</h2>
  <p style="margin-top:28px">With nearly 40 years of dedicated solar experience, we're the top-rated* U.S. solar company with over 15,000 five-star reviews.*</p>
  <p>If you're considering solar, energy storage, or EV charging for your home, make sure you talk to Kelmatrix.</p>
  <p>With nearly 40 years of dedicated solar experience, we're the top-rated* U.S. solar company with over 15,000 five-star reviews.*</p>
  <p>If you're considering solar, energy storage, or EV charging for your home, make sure you talk to Kelmatrix</p>
</div>
<div class="abs split-img" style="left:600px;top:3014px;background:linear-gradient(135deg,#5a6678 0%,#8f97a3 40%,#d9a73a 70%,#b2802a 100%)" role="img" aria-label="Close-up photo of a gloved hand tightening a solar panel clamp"></div>

<footer class="abs footer"></footer>
<div class="abs col" style="left:188px"><h4>FIND US HERE</h4><ul><li>U.S. Kelmatrix Dealer Locations</li><li>Find Kelmatrix in these states:</li><li>Alabama</li><li>Alaska</li><li>Arizona</li><li>Arkansas</li></ul></div>
<div class="abs col" style="left:446px"><h4>HERE</h4><ul><li>California</li><li>Colorado</li><li>Connecticut</li><li>Delaware</li><li>Florida</li><li>Georgia</li><li>Hawaii</li><li>Idaho</li></ul></div>
<div class="abs col" style="left:599px"><h4>CONTACT</h4><ul><li>Av. Orvalho Prado 218 / 305</li><li>Ravenda – Lumeira – PA – Brasil</li><li>CEP: 61420-000</li><li>Email address: contact@nuvaro.ee</li><li>Phone: +55.91.4720-1183</li><li>Whatsapp: +55.91.9034-5521</li><li>Callio: nuvaross</li></ul></div>
<div class="abs col" style="left:860px"><h4>KEEP CONNECTED</h4><ul><li class="icon"><i></i>Follow us on Chirpline</li><li class="icon"><i></i>Follow us on Worknet</li><li class="icon"><i></i>Like us on Friendwall</li><li class="icon"><i></i>Subscribe to our feed</li><li class="icon"><i></i>Pin us on Pinboardly</li></ul></div>
<div class="abs rule"></div>
<div class="abs copy">Copyright @ Nuvaro.ee</div>
<div class="abs legal">Terms of Use &nbsp; | &nbsp; Privacy Policy</div>

</body>
</html>
```